QP Fiduciary Website Redesign Contest

We want to refresh our website to be more insitutional, professional for an international audience. We have designed a new logo for this purpose and that has been attached. A full brand brief and positioning statement has also been attached. Please read through all the documents carefully before designing. The old website is found here: https://qp-fiduciary.example/

Target Market(s)

Actuaries and associated businesses internationally

Industry/Entity Type

professional services - actuaries

Number of Pages Required

3 page

Font styles to use
Sans Serif

Colors
0054AA
0677BA
7BADD7
CADEEF
E8F1F8
0094D4
00A9DD
6FCCEA
C7EBF8
E9F6FB
F0912C
F2A743
F7CA91
FBE8D2
FDF5EE
EE7325
F08F49
F5BC92
FAE3D3
FDF4ED
EB3D1F
EC4F4E
F09395
F8D3D4
FCEDEE

Requirements
Must have
• blues and greens to match the logo color, complimentary colors, navigation
Nice to have
• old site: https://qp-fiduciary.example/

```html
<!DOCTYPE html>
<html lang="en">
<head>
<meta charset="utf-8">
<title>QP Fiduciary — Actuarial Software</title>
<link rel="stylesheet" href="https://fonts.googleapis.com/css2?family=Archivo:wght@400;500;700;800&family=Inter:wght@400;500;600;700&display=swap">
<style>
:root{
  --orange:#EE5A12;
  --orange-soft:#F08F49;
  --navy:#14114A;
  --navy-mid:#252263;
  --ink:#0B0C22;
  --green:#2A6534;
  --gray-band:#EDEDED;
  --text:#1A1A1A;
  --muted:#6B6B6B;
  --line:#E3E3E3;
  --date:#1E3C86;
  --white:#FFFFFF;
}
*{box-sizing:border-box;margin:0;padding:0}
html,body{width:1200px;height:4428px;overflow:hidden}
body{position:relative;background:var(--white);font-family:'Inter',sans-serif;color:var(--text)}
.abs{position:absolute}
h1,h2,h3,.brand{font-family:'Archivo',sans-serif}
.section-title{position:absolute;left:0;width:1200px;text-align:center;font-size:38px;font-weight:400;color:var(--text)}
.section-title b{font-weight:800}
.btn{position:absolute;display:flex;align-items:center;justify-content:center;gap:10px;border-radius:30px;background:var(--orange);color:#fff;font-weight:600;font-size:15px;text-decoration:none}
.btn .arrow{width:15px;height:15px;border-radius:50%;background:#fff;position:relative}
.btn .arrow::after{content:"";position:absolute;left:4px;top:4px;border-left:6px solid var(--orange);border-top:3.5px solid transparent;border-bottom:3.5px solid transparent}

/* header */
.site-header{position:absolute;top:0;left:0;width:1200px;height:103px;background:#fff}
.brand{font-weight:700;font-size:28px;letter-spacing:.5px;color:var(--navy)}
.nav{position:absolute;left:358px;top:43px;display:flex;gap:24px;font-size:14px;font-weight:500}
.nav a{color:var(--text);text-decoration:none}
.nav a.active{color:var(--orange)}

/* hero */
.hero{position:absolute;top:103px;left:0;width:1200px;height:640px;clip-path:polygon(0 0,100% 0,100% 530px,0 640px)}
.hero-visual{position:absolute;inset:0;background:
  radial-gradient(ellipse 520px 300px at 1000px 260px,rgba(40,120,230,.55),transparent 70%),
  radial-gradient(ellipse 700px 200px at 700px 520px,rgba(30,90,200,.45),transparent 70%),
  linear-gradient(180deg,#03060F 0%,#061230 70%,#0A1F52 100%)}
.hero h1{position:absolute;left:150px;top:92px;width:560px;font-size:47px;line-height:61px;font-weight:400;color:#fff}
.hero h1 b{font-weight:800}
.hero p{position:absolute;left:150px;top:295px;width:440px;font-size:13.5px;line-height:22px;color:#fff;font-weight:500}

/* develops */
.develop-copy{position:absolute;top:905px;left:250px;width:700px;text-align:center;font-size:13px;line-height:20px;color:var(--muted)}
.globe{position:absolute;left:129px;top:985px;width:362px;height:362px;border-radius:50%;background:radial-gradient(circle at 40% 40%,#3A3D8C 0%,#1B1C5A 55%,#0E0E38 100%)}
.service{position:absolute;left:610px;width:460px;height:62px}
.service .dot{position:absolute;left:0;top:0;width:62px;height:62px;border-radius:50%;background:var(--green);display:flex;align-items:center;justify-content:center}
.service h3{position:absolute;left:91px;top:-3px;font-size:15px;font-weight:700}
.service p{position:absolute;left:91px;top:19px;width:340px;font-size:11px;line-height:17px;color:var(--muted)}

/* core */
.card{position:absolute;top:1590px;width:285px;height:310px;border:1.5px solid var(--line);border-radius:26px;background:#fff;text-align:center}
.card.featured{border-color:var(--orange)}
.card .icon{position:absolute;left:86px;top:40px;width:112px;height:112px;border-radius:50%;background:var(--navy);box-shadow:0 0 0 6px #E4E4EC;display:flex;align-items:center;justify-content:center}
.card.featured .icon{background:var(--orange);box-shadow:0 0 0 6px #FBE1D2}
.card h3{position:absolute;top:173px;left:0;width:100%;font-size:17px;font-weight:700}
.card p{position:absolute;top:210px;left:30px;width:225px;font-size:13px;line-height:20px;color:var(--muted)}

/* platform */
.platform{position:absolute;top:2008px;left:0;width:1200px;height:686px;background:var(--navy)}
.platform .section-title{color:#fff;top:130px}
.feature{position:absolute;color:#fff}
.feature h3{font-size:16px;font-weight:500;font-family:'Inter',sans-serif}
.feature p{font-size:11px;line-height:16px;color:#D8D8E8;margin-top:6px}
.feature-icon{position:absolute;width:76px;height:76px;border-radius:50%;background:var(--orange);display:flex;align-items:center;justify-content:center}
.hub{position:absolute;left:488px;top:285px;width:224px;height:224px;border-radius:50%;background:#fff;display:flex;align-items:center;justify-content:center}

/* articles */
.feature-article{position:absolute;left:156px;top:2960px;width:423px;height:468px;border:2px solid var(--orange);border-radius:22px;background:linear-gradient(160deg,#2A2775 0%,#3A37A8 55%,#4B45C0 100%)}
.article{position:absolute;left:608px;width:450px;height:140px}
.article .thumb{position:absolute;left:0;top:0;width:150px;height:140px;border-radius:22px;border:2px solid #3A5BC0}
.article .date{position:absolute;left:174px;top:10px;font-size:13px;font-weight:600;color:var(--date)}
.article h3{position:absolute;left:174px;top:36px;width:270px;font-size:16.5px;line-height:22px;font-weight:700}
.article p{position:absolute;left:174px;top:88px;width:270px;font-size:13px;line-height:19px;color:var(--muted)}
.outline-btn{position:absolute;left:517px;top:3474px;width:183px;height:47px;border:2px solid var(--text);border-radius:30px;display:flex;align-items:center;justify-content:center;gap:10px;font-weight:600;font-size:15px}
.outline-btn .arrow{width:14px;height:14px;border-radius:50%;background:var(--text);position:relative}
.outline-btn .arrow::after{content:"";position:absolute;left:4px;top:4px;border-left:5px solid #fff;border-top:3px solid transparent;border-bottom:3px solid transparent}

/* footer */
.footer-bg{position:absolute;top:3780px;left:0;width:1200px;height:648px;background:var(--ink);clip-path:polygon(0 107px,100% 50px,100% 100%,0 100%)}
.cta{position:absolute;left:156px;top:3639px;width:891px;height:361px;border:2px solid var(--orange);border-radius:24px;background:radial-gradient(circle at 80% 20%,#33307A,transparent 60%),var(--navy-mid)}
.cta h2{position:absolute;top:100px;width:100%;text-align:center;color:#fff;font-size:38px;line-height:57px;font-weight:700}
.foot-head{position:absolute;top:4090px;font-family:'Archivo',sans-serif;font-weight:700;font-size:17px;color:#fff}
.foot-item{position:absolute;left:620px;font-size:12px;line-height:18px;color:#fff}
.foot-links{position:absolute;left:920px;top:4140px;list-style:none;font-size:13px;line-height:29px;color:#fff}
.foot-divider{position:absolute;left:150px;top:4346px;width:900px;height:1px;background:#3A3B55}
.copyright{position:absolute;top:4376px;left:0;width:1200px;text-align:center;font-size:12px;color:#fff}
</style>
</head>
<body>

<header class="site-header">
  <div class="brand abs" style="left:48px;top:32px">QP Fiduciary</div>
  <nav class="nav">
    <a class="active" href="#">Home</a><a href="#">Platform</a><a href="#">Solutions</a><a href="#">Insights</a><a href="#">Company</a><a href="#">Contact</a>
  </nav>
  <a class="btn" href="#" style="left:828px;top:29px;width:322px;height:48px">Request a Technical Walkthrough <span class="arrow"></span></a>
</header>

<section class="hero">
  <div class="hero-visual" role="img" aria-label="Glowing blue financial chart and data particles on a dark background"></div>
  <h1>Actuarial Software <b>For Structured, Auditable Financial Analysis</b></h1>
  <p>Software that translates actuarial methodologies into disciplined decision-ready analytical tools across diverse regulatory environments</p>
  <a class="btn" href="#" style="left:150px;top:388px;width:323px;height:48px">Request a Technical Walkthrough <span class="arrow"></span></a>
</section>
<svg class="abs" style="left:0;top:600px" width="1200" height="160" viewBox="0 0 1200 160">
  <polygon points="250,130 1200,40 1200,60 250,148" fill="var(--gray-band)"/>
  <polygon points="739,105 1200,65 1200,143" fill="var(--green)"/>
</svg>

<h2 class="section-title" style="top:835px"><b>QP Fiduciary</b> develops</h2>
<p class="develop-copy">QP Fiduciary develops modular actuarial software designed to support reserving, valuation, pricing, and risk analysis workflows across diverse regulatory environments.</p>
<div class="globe" role="img" aria-label="Globe of connected data points representing international coverage"></div>
<svg class="abs" style="left:490px;top:1030px" width="125" height="280" viewBox="0 0 125 280" fill="none" stroke="#C9C9C9" stroke-dasharray="5 4">
  <path d="M0 150 H40 V12 H120 M40 96 H120 M0 156 H60 M40 160 V266 H120 M40 180 H120"/>
</svg>
<div class="service" style="top:1010px"><div class="dot"><svg width="34" height="34" viewBox="0 0 34 34" fill="none" stroke="#fff" stroke-width="1.6"><circle cx="17" cy="17" r="6"/><circle cx="17" cy="17" r="12" stroke-dasharray="4 3"/></svg></div><h3>Support Reserving</h3><p>Nemo enim ipsam voluptatem quia voluptas sit aspernatur aut odit aut fugit, sed quia consequuntur magni dolores</p></div>
<div class="service" style="top:1094px"><div class="dot"><svg width="34" height="34" viewBox="0 0 34 34" fill="none" stroke="#fff" stroke-width="1.6"><circle cx="17" cy="17" r="6"/><circle cx="17" cy="17" r="12" stroke-dasharray="4 3"/></svg></div><h3>Valuation</h3><p>Nemo enim ipsam voluptatem quia voluptas sit aspernatur aut odit aut fugit, sed quia consequuntur magni dolores</p></div>
<div class="service" style="top:1179px"><div class="dot"><svg width="34" height="34" viewBox="0 0 34 34" fill="none" stroke="#fff" stroke-width="1.6"><circle cx="17" cy="17" r="6"/><circle cx="17" cy="17" r="12" stroke-dasharray="4 3"/></svg></div><h3>Pricing</h3><p>Nemo enim ipsam voluptatem quia voluptas sit aspernatur aut odit aut fugit, sed quia consequuntur magni dolores</p></div>
<div class="service" style="top:1263px"><div class="dot"><svg width="34" height="34" viewBox="0 0 34 34" fill="none" stroke="#fff" stroke-width="1.6"><circle cx="17" cy="17" r="6"/><circle cx="17" cy="17" r="12" stroke-dasharray="4 3"/></svg></div><h3>Risk Analysis</h3><p>Nemo enim ipsam voluptatem quia voluptas sit aspernatur aut odit aut fugit, sed quia consequuntur magni dolores</p></div>

<h2 class="section-title" style="top:1500px"><b>Core</b> Solutions</h2>
<div class="card" style="left:151px"><div class="icon"><svg width="50" height="50" viewBox="0 0 50 50" fill="none" stroke="#fff" stroke-width="2"><rect x="10" y="8" width="30" height="34" rx="3"/><path d="M16 18h18M16 25h18M16 32h10"/></svg></div><h3>Reserving &amp; Valuation</h3><p>Software supporting structured reserving workflows and financial reporting across jurisdictions.</p></div>
<div class="card featured" style="left:457px"><div class="icon"><svg width="50" height="50" viewBox="0 0 50 50" fill="none" stroke="#fff" stroke-width="2"><rect x="10" y="6" width="26" height="36" rx="3"/><path d="M16 15h14M16 22h14M16 29h8"/><circle cx="36" cy="36" r="7"/></svg></div><h3>Pricing</h3><p>Models supporting insurance and reinsurance pricing based on actuarial methodologies.</p></div>
<div class="card" style="left:762px"><div class="icon"><svg width="50" height="50" viewBox="0 0 50 50" fill="none" stroke="#fff" stroke-width="2"><circle cx="25" cy="22" r="12"/><circle cx="25" cy="22" r="4"/><path d="M20 36h10M21 41h8"/></svg></div><h3>Enterprise Risk Management</h3><p>Software supporting reinsurance optimization and capital modeling</p></div>

<section class="platform">
  <h2 class="section-title"><b>Platform</b> Characteristics</h2>
  <svg class="abs" style="left:0;top:0" width="1200" height="686" viewBox="0 0 1200 686" fill="none">
    <circle cx="600" cy="397" r="139" stroke="#8E8DB0" stroke-width="2"/>
    <g stroke="#C9C9D8" stroke-width="2">
      <path d="M191 313 V382 H423 M191 479 V407 H423 M1009 313 V382 H778 M1009 479 V407 H778"/>
    </g>
    <g fill="var(--orange)">
      <circle cx="462" cy="310" r="5"/><circle cx="742" cy="310" r="5"/><circle cx="462" cy="467" r="5"/><circle cx="742" cy="467" r="5"/>
      <circle cx="191" cy="479" r="4"/><circle cx="1009" cy="313" r="4"/><circle cx="1009" cy="479" r="4"/>
    </g>
  </svg>
  <div class="hub"><span class="brand" style="font-size:24px;color:var(--navy)">QP Fiduciary</span></div>

  <div class="feature-icon" style="left:152px;top:237px"><svg width="40" height="40" viewBox="0 0 40 40" fill="none" stroke="#fff" stroke-width="1.8"><rect x="15" y="4" width="10" height="10"/><rect x="4" y="26" width="10" height="10"/><rect x="26" y="26" width="10" height="10"/><path d="M20 14v6M9 26v-6h22v6"/></svg></div>
  <div class="feature" style="left:244px;top:250px;width:200px"><h3>Structured Workflows</h3><p>Lorem ipsum dolor sit amet, consectetur adipiscing elit, sed do eiusmod tempor</p></div>

  <div class="feature-icon" style="left:152px;top:479px"><svg width="40" height="40" viewBox="0 0 40 40" fill="none" stroke="#fff" stroke-width="1.8"><rect x="6" y="6" width="22" height="28" rx="2"/><circle cx="24" cy="22" r="7"/><path d="M29 27l6 6"/></svg></div>
  <div class="feature" style="left:244px;top:467px;width:200px"><h3>Transparent Assumptions</h3><p>Lorem ipsum dolor sit amet, consectetur adipiscing elit, sed do eiusmod tempor</p></div>

  <div class="feature-icon" style="left:972px;top:237px"><svg width="40" height="40" viewBox="0 0 40 40" fill="none" stroke="#fff" stroke-width="1.8"><circle cx="20" cy="15" r="8"/><path d="M6 36c2-8 8-11 14-11s12 3 14 11"/></svg></div>
  <div class="feature" style="left:736px;top:236px;width:220px;text-align:right"><h3>Multi-jurisdictional Review Support</h3><p>Lorem ipsum dolor sit amet consectetur adipiscing elit, sed do eiusmod tempor</p></div>

  <div class="feature-icon" style="left:972px;top:479px"><svg width="40" height="40" viewBox="0 0 40 40" fill="none" stroke="#fff" stroke-width="1.8"><rect x="4" y="6" width="14" height="12"/><rect x="22" y="6" width="14" height="12"/><rect x="8" y="24" width="24" height="12"/></svg></div>
  <div class="feature" style="left:736px;top:478px;width:220px;text-align:right"><h3>Comparative Analysis Capability</h3><p>Lorem ipsum dolor sit amet consectetur adipiscing elit, sed</p></div>
</section>

<h2 class="section-title" style="top:2855px"><b>Recent Articles</b></h2>
<div class="feature-article" role="img" aria-label="Abstract layered purple geometric shapes"></div>
<article class="article" style="top:2960px"><div class="thumb" role="img" aria-label="Flowing blue light waves" style="background:linear-gradient(135deg,#0A1140,#1F3FB0 60%,#0A1140)"></div><div class="date">Mar 13 2026</div><h3>Methodological perspectives in actuarial reserving</h3><p>Sed ut perspiciatis unde omnis iste natus error sit voluptatem accusantium</p></article>
<article class="article" style="top:3123px"><div class="thumb" role="img" aria-label="Abstract blue folded sculpture" style="background:linear-gradient(135deg,#0C1A4A,#2F7FD8 55%,#0C1A4A)"></div><div class="date">Mar 13 2026</div><h3>Governance considerations in multi-jurisdictional analysis</h3><p>Sed ut perspiciatis unde omnis iste natus error sit voluptatem accusantium</p></article>
<article class="article" style="top:3287px"><div class="thumb" role="img" aria-label="Pink and blue light streams" style="background:linear-gradient(135deg,#2A0C40,#C03AA8 45%,#2A5BD0 80%,#0A1140)"></div><div class="date">Mar 13 2026</div><h3>Observations on actuarial practice in emerging markets</h3><p>Sed ut perspiciatis unde omnis iste natus error sit voluptatem accusantium</p></article>
<a class="outline-btn" href="#" style="color:var(--text);text-decoration:none">Read Insights <span class="arrow"></span></a>

<svg class="abs" style="left:0;top:3780px" width="160" height="120" viewBox="0 0 160 120">
  <polygon points="0,5 160,22 160,78 0,85" fill="var(--green)"/>
  <polygon points="0,85 160,78 160,98 0,107" fill="var(--gray-band)"/>
</svg>
<div class="footer-bg"></div>

<section class="cta">
  <h2>Interested in Exploring<br>The Platform?</h2>
  <a class="btn" href="#" style="left:269px;top:237px;width:347px;height:48px">Request a Technical Walkthrough <span class="arrow"></span></a>
</section>

<footer>
  <div class="brand abs" style="left:150px;top:4158px;font-size:38px;color:#fff">QP Fiduciary</div>
  <div class="abs" style="left:150px;top:4246px;width:40px;height:40px;border-radius:50%;background:var(--green)" aria-label="Social profile"></div>

  <div class="foot-head" style="left:595px">LOCATION</div>
  <svg class="abs" style="left:594px;top:4146px" width="12" height="16" viewBox="0 0 12 16"><path d="M6 0a6 6 0 0 1 6 6c0 4-6 10-6 10S0 10 0 6a6 6 0 0 1 6-6z" fill="var(--orange)"/><circle cx="6" cy="6" r="2" fill="var(--ink)"/></svg>
  <p class="foot-item" style="top:4142px">Nemo enim ipsam voluptatem<br>voluptas sit aspernatur<br>25486</p>
  <svg class="abs" style="left:594px;top:4214px" width="13" height="13" viewBox="0 0 24 24"><path d="M6.6 10.8a15 15 0 0 0 6.6 6.6l2.2-2.2c.3-.3.7-.4 1-.2 1.1.4 2.3.6 3.6.6.6 0 1 .4 1 1V20c0 .6-.4 1-1 1A17 17 0 0 1 3 4c0-.6.4-1 1-1h3.5c.6 0 1 .4 1 1 0 1.3.2 2.5.6 3.6.1.3 0 .7-.2 1z" fill="var(--orange)"/></svg>
  <p class="foot-item" style="top:4210px">Call Us:<br>+1 555-010-0199</p>
  <svg class="abs" style="left:594px;top:4271px" width="14" height="11" viewBox="0 0 14 11"><rect width="14" height="11" rx="1.5" fill="var(--orange)"/><path d="M1 1.5l6 4.5 6-4.5" stroke="var(--ink)" stroke-width="1.2" fill="none"/></svg>
  <p class="foot-item" style="top:4268px">Email Us:<br>info@qp-fiduciary.example</p>

  <div class="foot-head" style="left:920px">LINKS</div>
  <ul class="foot-links"><li>Company</li><li>Platform</li><li>Solutions</li><li>Insights</li><li>Contact</li></ul>

  <div class="foot-divider"></div>
  <p class="copyright">2026 © QP Fiduciary . All Rights Reserved</p>
</footer>

</body>
</html>
```